Business Card - high end, modern health care

Hey designers!

We need a double sided business card for the boutique, cutting edge physical therapy rehabilitation centre in Sydney's Northern Beaches.

With the most qualified physios in the area The Harbourview Motion Clinic does what other physiotherapy practices do not, we take our time with our patients giving them longer appointments, better physios and therefor faster results!

We guarantee that the service people receive at THMC will be unparalleled.

Hence we need a business card to reflect our modern, boutique, high end service. The final design needs to reflect that we are in a class of our own yet with the feel of beachside retreat.

Below I have attached our logo in both blue on white and white on blue. The exact colour is;
and the font that we have used in our logo is Tex Gyre Aventador.

I like the idea of the blue as the main colour as it is more eye catching and our signage onto the main road will be in this blue and in the interest of consistency across marketing the blue needs to be a part of the design. However I would appreciate a few designs onto a wooden background as this is a visual theme within the fitout of the practice.

The design needs to be of standard size (91x55mm).

Target Market(s)

We target people who have an end outcome in mind and those who have had poor experiences with other providers and ensure that everyone gets the care that they deserve with a premium service that is tailored to the individuals circumstances. As a premium service, the target market is highly educated, business and tech savvy with the additional target market of elderly people who have self funded their retirement and see value in paying for the best ongoing rehabilitation to maintain independence.

Industry/Entity Type

Physical Therapy

Contact Information for Business Card

Name, designation( Titled Musculoskeletal Physiotherapist... there will also be those in the company that have multiple designations ie 5 or 6 words long), phone number, email, facebook, instagram, address

Font styles to use
Sans Serif

Colors

Designer to choose colors to be used in the design.

Requirements
Must have
• Front - The logo as large as possible, blue or wooden theme, and all of the important details.
• Back - A blank space/lines on which to write appointment times (no "Appointment, date, time" etc.)
Nice to have
• facebook url
• logos for facebook and instagram
• Mini logos for the phone and email?

```html
<!DOCTYPE html>
<html lang="en">
<head>
<meta charset="utf-8">
<title>The Harbourview Motion Clinic – Business Card</title>
<link rel="stylesheet" href="https://fonts.googleapis.com/css2?family=Lato:wght@400;700;900&display=swap">
<style>
  :root {
    --backdrop: #8c8c8c;
    --card-light: #f3f3f3;
    --brand-blue: #0057a8;
    --ink: #2b2b2b;
    --white: #ffffff;
    --rule: #555555;
  }
  * { margin: 0; padding: 0; box-sizing: border-box; }
  html, body { width: 1200px; height: 1200px; overflow: hidden; }
  body {
    position: relative;
    background: var(--backdrop);
    font-family: "Lato", Arial, sans-serif;
    color: var(--ink);
  }
  .card {
    position: absolute;
    top: 310px;
    height: 594px;
    border-radius: 18px;
    overflow: hidden;
  }
  .card-front { left: 234px; width: 363px; background: var(--card-light); }
  .card-back  { left: 627px; width: 370px; background: var(--brand-blue); }

  /* front */
  .brand-mark {
    position: absolute;
    left: 74px; top: 54px;
    width: 216px; height: 216px;
    border-radius: 50%;
    background: var(--brand-blue);
    display: flex; align-items: center; justify-content: center;
    text-align: center;
  }
  .brand-mark-name {
    color: var(--white);
    font-weight: 700;
    font-size: 19px;
    line-height: 1.25;
    letter-spacing: 0.5px;
  }
  .person-name {
    position: absolute; left: 0; right: 0; top: 320px;
    text-align: center;
    color: var(--brand-blue);
    font-weight: 700;
    font-size: 23px;
  }
  .person-role {
    position: absolute; left: 0; right: 0; top: 345px;
    text-align: center;
    font-size: 17px;
  }
  .divider {
    position: absolute; left: 82px; width: 200px; height: 20px;
    display: flex; align-items: center; gap: 6px;
  }
  .divider-contact { top: 386px; }
  .divider-social { top: 475px; }
  .divider-line { flex: 1; height: 1px; background: var(--rule); }
  .divider-icon { width: 19px; height: 19px; display: block; }
  .contact-line {
    position: absolute; left: 0; right: 0;
    text-align: center;
    font-size: 17px;
  }
  .contact-phone { top: 408px; }
  .contact-email { top: 430px; }
  .social-line {
    position: absolute; left: 0; right: 0;
    text-align: center;
    font-size: 16.5px;
  }
  .social-page { top: 505px; }
  .social-handle { top: 526px; }

  /* back */
  .back-mark {
    position: absolute;
    left: 85px; top: 72px;
    width: 200px; height: 200px;
    border-radius: 50%;
    background: var(--white);
  }
  .back-name {
    position: absolute; left: 0; right: 0; top: 291px;
    text-align: center;
    color: var(--white);
  }
  .back-name-main { display: block; font-size: 25px; line-height: 29px; font-weight: 700; }
  .back-name-sub  { display: block; font-size: 15px; letter-spacing: 4px; line-height: 18px; font-weight: 400; }
  .appointment-panel {
    position: absolute; left: 0; right: 0; top: 399px; height: 167px;
    background: var(--white);
  }
  .write-field {
    position: absolute; left: 64px;
    display: flex; align-items: flex-end;
    font-size: 20px;
    color: #111;
  }
  .write-field-date { top: 31px; }
  .write-field-time { top: 104px; }
  .write-line {
    display: block;
    width: 189px; height: 2px;
    background: #111;
    margin-bottom: 4px;
  }
</style>
</head>
<body>

  <section class="card card-front" aria-label="Card front">
    <div class="brand-mark">
      <span class="brand-mark-name">The Harbourview<br>Motion Clinic</span>
    </div>

    <h1 class="person-name">DANIEL CARTER</h1>
    <p class="person-role">Managing Director</p>

    <div class="divider divider-contact">
      <span class="divider-line"></span>
      <svg class="divider-icon" viewBox="0 0 20 20" aria-hidden="true">
        <circle cx="10" cy="10" r="8.5" fill="none" stroke="var(--brand-blue)" stroke-width="1.6"/>
        <path d="M7 5.5 L8.6 5.2 L9.4 7.6 L8.3 8.5 Q9.2 10.6 11.4 11.7 L12.4 10.6 L14.7 11.5 L14.4 13.1 Q13.6 14.4 11.8 14 Q7.2 12.4 6 8 Q5.7 6.2 7 5.5 Z" fill="var(--brand-blue)"/>
      </svg>
      <svg class="divider-icon" viewBox="0 0 20 20" aria-hidden="true">
        <circle cx="10" cy="10" r="8.5" fill="none" stroke="var(--brand-blue)" stroke-width="1.6"/>
        <rect x="5.3" y="6.6" width="9.4" height="6.8" rx="0.8" fill="var(--brand-blue)"/>
        <path d="M5.6 7 L10 10.4 L14.4 7" fill="none" stroke="var(--white)" stroke-width="1"/>
      </svg>
      <span class="divider-line"></span>
    </div>
    <p class="contact-line contact-phone">444 555 7719</p>
    <p class="contact-line contact-email">info@harbourviewmotion.com</p>

    <div class="divider divider-social">
      <span class="divider-line"></span>
      <svg class="divider-icon" viewBox="0 0 20 20" aria-hidden="true">
        <circle cx="10" cy="10" r="9.5" fill="var(--brand-blue)"/>
      </svg>
      <svg class="divider-icon" viewBox="0 0 20 20" aria-hidden="true">
        <circle cx="10" cy="10" r="9.5" fill="var(--brand-blue)"/>
      </svg>
      <span class="divider-line"></span>
    </div>
    <p class="social-line social-page">social.harbourviewmotion.com/clinic</p>
    <p class="social-line social-handle">follow@harbourviewmotionclinic</p>
  </section>

  <section class="card card-back" aria-label="Card back">
    <div class="back-mark"></div>
    <p class="back-name">
      <span class="back-name-main">THE HARBOURVIEW</span>
      <span class="back-name-sub">MOTION CLINIC</span>
    </p>
    <div class="appointment-panel">
      <div class="write-field write-field-date">DATE<span class="write-line"></span></div>
      <div class="write-field write-field-time">TIME<span class="write-line"></span></div>
    </div>
  </section>

</body>
</html>
```